Business card design needed

I run a Beautician studio (for 7 years now)
I offer
- Velmo Body Sugaring
- Ruby Glaze
- Nails
- Facials
- Manicure
- Foot Treatment
It might not be necessary to list all those treatments?
Maybe the link to the Website is sufficient?
I leave that up to you ...
(more info on www.FernAndDewByLenka.com.au)
Velmo BodySugaring is our biggest success, It replaces waxing.
I would like to incorporate the logo into the Business Card.
We had many complaints regarding our old Business Cards as the Phone Number was to small.
On the backside, we would like a "your next Appointment" section.
Looking forward to you Design, cheers ... Lenka
Industry/Entity Type
Business
Contact Information for Business Card
Fern by Dew by Lenka
14 Korrin Sqr 3942 Ashbury
www.FernAndDewByLenka.com.au
03 9481 2267

```html
<!DOCTYPE html>
<html lang="en">
<head>
<meta charset="utf-8">
<title>Fern by Dew by Lenka – Business Cards</title>
<link rel="stylesheet" href="https://fonts.googleapis.com/css2?family=Arimo:wght@400;700&family=Source+Sans+3:wght@400;600;700&family=Marcellus&display=swap">
<style>
  :root{
    --stage:#161616;
    --stage-light:#262626;
    --card:#ffffff;
    --green:#109447;
    --green-band:#0f9a4a;
    --orange-top:#e5532b;
    --orange-mid:#f08f2a;
    --yellow-bottom:#f6d631;
    --ink:#222222;
    --grey:#555555;
    --brown:#6b4a2c;
    --line:#888888;
  }
  *{box-sizing:border-box;margin:0;padding:0}
  html,body{width:1200px;height:720px;overflow:hidden}
  body{
    position:relative;
    background:linear-gradient(90deg,var(--stage),var(--stage-light) 50%,var(--stage));
    font-family:"Source Sans 3",Arial,sans-serif;
    color:var(--ink);
  }
  .card{position:absolute;background:var(--card);border-radius:22px;overflow:hidden}
  .abs{position:absolute;white-space:nowrap}

  /* front card */
  .card--front{left:310px;top:30px;width:525px;height:300px;font-family:"Arimo",Arial,sans-serif}
  .studio-name{left:37px;top:97px;font-size:19px;font-weight:700;color:var(--green);letter-spacing:.3px}
  .studio-tag{left:42px;top:121px;font-size:13.5px;color:var(--ink)}
  .studio-phone{left:36px;top:151px;font-size:20px;display:flex;align-items:center;gap:6px}
  .studio-address{left:37px;top:181px;font-size:18px}
  .web-band{left:297px;top:22px;width:23px;height:255px;background:var(--green-band)}
  .web-band span{position:absolute;left:50%;top:50%;transform:translate(-50%,-50%) rotate(-90deg);
    color:#fff;font-size:12.5px;white-space:nowrap}
  .treat-panel{left:322px;top:22px;width:201px;height:255px;
    background:linear-gradient(180deg,var(--orange-top),var(--orange-mid) 55%,var(--yellow-bottom))}
  .treat-brand{position:absolute;left:0;right:0;top:22px;text-align:center}
  .treat-title{left:14px;top:136px;font-size:17px;font-weight:700;color:var(--ink);letter-spacing:.8px}
  .treat-list{left:14px;top:158px;list-style:none;font-size:14.5px;line-height:21px;color:var(--ink)}

  /* brand stand-in */
  .brand{display:flex;flex-direction:column;align-items:center;gap:8px}
  .brand-dot{width:44px;height:44px;border-radius:50%;background:var(--orange-mid)}
  .brand-name{font-family:"Source Sans 3",Arial,sans-serif;font-size:12px;font-weight:600;letter-spacing:1.6px;color:var(--brown);text-transform:uppercase}
  .treat-panel .brand-dot{background:var(--yellow-bottom)}

  /* back cards */
  .card--appt{left:57px;top:367px;width:525px;height:298px}
  .card--note{left:611px;top:367px;width:524px;height:300px}
  .hours-title{font-family:"Arimo",Arial,sans-serif;font-size:21px;color:var(--green);letter-spacing:1.2px}
  .hours-line{font-size:16px;font-weight:600;color:var(--grey)}
  .appt-title{left:35px;top:94px;font-family:"Marcellus",serif;font-size:19px;color:var(--green);letter-spacing:.5px}
  .label{font-size:15px;color:var(--grey)}
  .dotted{position:absolute;border-bottom:1px dotted var(--line)}
  .rule{position:absolute;border-bottom:1px solid var(--line)}
  .box{position:absolute;border:1px solid var(--line);border-radius:2px}
  .day{font-size:15px;font-weight:600;color:var(--grey)}
  .notice{left:0;right:0;top:276px;text-align:center;font-size:12px;color:var(--ink)}
  .divider{left:258px;top:38px;width:1px;height:226px;background:#bbbbbb}
  .note-text{font-size:15.5px;color:var(--grey);line-height:21px}
</style>
</head>
<body>

<section class="card card--front">
  <div class="abs studio-name">FERN BY DEW BY LENKA</div>
  <div class="abs studio-tag">In the heart of Merrindale</div>
  <div class="abs studio-phone">
    <svg width="18" height="18" viewBox="0 0 24 24" aria-hidden="true"><path d="M6.6 10.8a15 15 0 0 0 6.6 6.6l2.2-2.2a1 1 0 0 1 1-.25 11.4 11.4 0 0 0 3.6.57 1 1 0 0 1 1 1V20a1 1 0 0 1-1 1A17 17 0 0 1 3 4a1 1 0 0 1 1-1h3.5a1 1 0 0 1 1 1c0 1.25.2 2.45.57 3.57a1 1 0 0 1-.25 1z" fill="none" stroke="#222" stroke-width="1.8"/></svg>
    03 9481 2267
  </div>
  <div class="abs studio-address">14 Korrin Sqr 3942 Ashbury</div>
  <div class="abs web-band"><span>www.FernAndDewByLenka.com.au</span></div>
  <div class="abs treat-panel">
    <div class="treat-brand"><div class="brand"><div class="brand-dot"></div><div class="brand-name">Velmo Body Sugaring</div></div></div>
    <div class="abs treat-title">Treatments offered</div>
    <ul class="abs treat-list">
      <li>• Velmo Body Sugaring</li>
      <li>• Ruby Glaze • Nails</li>
      <li>• Facials • Manicure</li>
      <li>• Foot Treatment</li>
    </ul>
  </div>
</section>

<section class="card card--appt">
  <div class="abs hours-title" style="left:31px;top:10px">Hours of Operation</div>
  <div class="abs hours-line" style="left:31px;top:38px">Mon - Fri: 7.30am - 7.00pm</div>
  <div class="abs hours-line" style="left:31px;top:60px">Saturday: 7.30am - 12.00pm</div>
  <div class="abs" style="left:330px;top:22px;width:150px"><div class="brand"><div class="brand-dot"></div><div class="brand-name">Velmo Body Sugaring</div></div></div>
  <div class="abs appt-title">YOUR APPOINTMENT</div>

  <div class="abs label" style="left:35px;top:132px">Name :</div>
  <div class="dotted" style="left:93px;top:146px;width:290px"></div>

  <div class="abs label" style="left:35px;top:170px">Date :</div>
  <div class="rule" style="left:93px;top:183px;width:95px"></div>
  <div class="abs label" style="left:194px;top:170px">Time :</div>
  <div class="rule" style="left:239px;top:183px;width:88px"></div>
  <div class="abs label" style="left:330px;top:170px">am / pm</div>

  <div class="abs label" style="left:35px;top:206px">Next Appointment</div>
  <div class="box" style="left:175px;top:206px;width:95px;height:20px"></div>
  <div class="box" style="left:301px;top:206px;width:95px;height:20px"></div>

  <div class="abs day" style="left:31px;top:244px">MON</div><div class="box" style="left:76px;top:245px;width:32px;height:20px"></div>
  <div class="abs day" style="left:115px;top:244px">TUE</div><div class="box" style="left:152px;top:245px;width:32px;height:20px"></div>
  <div class="abs day" style="left:191px;top:244px">WED</div><div class="box" style="left:233px;top:245px;width:32px;height:20px"></div>
  <div class="abs day" style="left:272px;top:244px">THU</div><div class="box" style="left:312px;top:245px;width:32px;height:20px"></div>
  <div class="abs day" style="left:352px;top:244px">FRI</div><div class="box" style="left:382px;top:245px;width:32px;height:20px"></div>
  <div class="abs day" style="left:422px;top:244px">SAT</div><div class="box" style="left:456px;top:245px;width:32px;height:20px"></div>

  <div class="abs notice">It would be appreciated if 24 hours notice could be given if you are unable to attend an appointment</div>
</section>

<section class="card card--note">
  <div class="abs hours-title" style="left:34px;top:59px">Hours of Operation</div>
  <div class="abs hours-line" style="left:34px;top:87px">Mon - Fri: 7.30am - 7.00pm</div>
  <div class="abs hours-line" style="left:34px;top:108px">Saturday: 7.30am - 12.00pm</div>
  <div class="abs" style="left:38px;top:150px;width:120px"><div class="brand"><div class="brand-dot"></div><div class="brand-name">Velmo Body Sugaring</div></div></div>

  <div class="abs divider"></div>

  <div class="dotted" style="left:276px;top:45px;width:218px"></div>
  <div class="abs" style="left:276px;top:53px;font-size:15px;font-weight:600;color:var(--grey)">has an appointment</div>

  <div class="abs day" style="left:276px;top:95px;font-size:14px">MON</div><div class="box" style="left:285px;top:119px;width:16px;height:10px"></div>
  <div class="abs day" style="left:323px;top:95px;font-size:14px">TUE</div><div class="box" style="left:328px;top:119px;width:16px;height:10px"></div>
  <div class="abs day" style="left:362px;top:95px;font-size:14px">WED</div><div class="box" style="left:368px;top:119px;width:16px;height:10px"></div>
  <div class="abs day" style="left:408px;top:95px;font-size:14px">THU</div><div class="box" style="left:414px;top:119px;width:16px;height:10px"></div>
  <div class="abs day" style="left:447px;top:95px;font-size:14px">FRI</div><div class="box" style="left:449px;top:119px;width:16px;height:10px"></div>
  <div class="abs day" style="left:481px;top:95px;font-size:14px">SAT</div><div class="box" style="left:485px;top:119px;width:16px;height:10px"></div>

  <div class="abs note-text" style="left:276px;top:143px">Date :</div>
  <div class="rule" style="left:318px;top:160px;width:152px"></div>
  <div class="abs note-text" style="left:276px;top:173px">Time :</div>
  <div class="rule" style="left:320px;top:190px;width:124px"></div>
  <div class="abs note-text" style="left:448px;top:173px">AM/PM</div>

  <div class="abs note-text" style="left:276px;top:215px">Advance notice requested for<br>appointment cancellation</div>
</section>

</body>
</html>
```